Velk Partners Building Business Cards

We need a business card that reflects our business as "Solar Experts" in San Diego. Browse our website www.velkpartners.example our License needs to be displayed as "CSLB# 3867140" our phone number is (619) 555-0187

Save thousands on your electric bills and increase the value of your home while helping to protect the environment. Our solar installation experts will help you design the system that's right for you, using only the highest quality equipment that will look great and give you ideal performance. Our goal is to make you energy independent, and get your electric bill to 0.

Paul Osterby
(619) 555-0187
paul@velkpartners.example

Target Market(s)

Home owners in san diego looking for solar

Industry/Entity Type

Solar Energy

Contact Information for Business Card

Paul Osterby
(619) 555-0187
paul@velkpartners.example

Font styles to use
Other font styles liked:
• Use our logo font

Requirements
Must have
• License needs to be displayed as "CSLB# 3867140" our phone number is (619) 555-0187
Nice to have
• Real images of rooftop home solar in san diego
Should not have
• our business address

```html
<!DOCTYPE html>
<html lang="en">
<head>
<meta charset="utf-8">
<title>Velk Partners Building — Business Card</title>
<link href="https://fonts.googleapis.com/css2?family=Source+Sans+3:wght@400;600;700&display=swap" rel="stylesheet">
<style>
  :root {
    --backdrop: #7d7d7d;
    --card-white: #ffffff;
    --navy: #1f3b7a;
    --sun: #f6ae0f;
    --ink: #1b1b1b;
    --sky-top: #2f7fd8;
    --sky-mid: #4a9ae6;
    --panel-deep: #1c3f8c;
    --panel-mid: #3b6cc4;
  }
  * { margin: 0; padding: 0; box-sizing: border-box; }
  html, body {
    width: 1200px; height: 900px; overflow: hidden;
    background: var(--backdrop);
    font-family: "Source Sans 3", "Helvetica Neue", Arial, sans-serif;
  }
  .stage { position: relative; width: 1200px; height: 900px; }
  .card {
    position: absolute; top: 170px; width: 347px; height: 560px; overflow: hidden;
  }
  .card-front { left: 259px; background: var(--card-white); }
  .card-back { left: 631px; }

  .top-band {
    position: absolute; left: 86px; top: 0; width: 178px; height: 56px;
    background: var(--navy);
  }
  .brand-block {
    position: absolute; left: 0; right: 0; top: 90px;
    display: flex; flex-direction: column; align-items: center;
  }
  .brand-dot {
    width: 96px; height: 96px; border-radius: 50%; background: var(--sun);
    margin-bottom: 22px;
  }
  .brand-name {
    font-weight: 700; font-size: 27px; color: var(--navy); line-height: 1;
  }
  .holder-name {
    position: absolute; left: 0; right: 0; top: 306px; text-align: center;
    font-weight: 600; font-size: 19px; color: var(--navy); letter-spacing: 0.2px;
  }
  .contact-list {
    position: absolute; left: 0; right: 0; top: 358px; list-style: none;
    text-align: center; font-size: 15px; color: var(--ink); line-height: 21px;
  }
  .contact-list svg { width: 14px; height: 12px; vertical-align: -1px; margin-right: 6px; fill: var(--navy); }
  .license {
    position: absolute; left: 0; right: 0; top: 428px; text-align: center;
    font-weight: 600; font-size: 17px; color: var(--navy);
  }
  .bottom-curve { position: absolute; left: 0; bottom: 0; width: 347px; height: 100px; }

  .back-photo {
    position: absolute; inset: 0;
    background: linear-gradient(160deg, var(--sky-top) 0%, var(--sky-mid) 32%, var(--panel-mid) 58%, var(--panel-deep) 100%);
  }
  .back-brand {
    position: absolute; left: 0; right: 0; top: 104px; text-align: center;
    font-weight: 700; font-size: 30px; color: var(--card-white); line-height: 1;
  }
</style>
</head>
<body>
<main class="stage">
  <section class="card card-front" aria-label="Card front">
    <div class="top-band"></div>
    <div class="brand-block">
      <span class="brand-dot"></span>
      <span class="brand-name">Velk Partners Building</span>
    </div>
    <h1 class="holder-name">PAUL OSTERBY</h1>
    <ul class="contact-list">
      <li><svg viewBox="0 0 14 12"><path d="M1 4c3-3 9-3 12 0l-1.5 1.6-2.2-.9V3.4H4.7v1.3l-2.2.9z M3 6h8l1 5H2z"/></svg>(619) 555-0187</li>
      <li><svg viewBox="0 0 14 12"><path d="M0 1h14v10H0z M1 2l6 5 6-5" fill="none" stroke="#1f3b7a" stroke-width="1.6"/><path d="M1 2l6 5 6-5z"/></svg>paul@velkpartners.example</li>
    </ul>
    <p class="license">License: CSLB# 3867140</p>
    <svg class="bottom-curve" viewBox="0 0 347 100" preserveAspectRatio="none">
      <path d="M0 80 C80 40 180 -10 260 20 C300 35 330 60 347 80 L347 100 L0 100 Z" fill="#1f3b7a"/>
    </svg>
  </section>

  <section class="card card-back" aria-label="Card back">
    <div class="back-photo" role="img" aria-label="Photo of rooftop solar panels under a clear blue sky"></div>
    <p class="back-brand">Velk Partners Building</p>
  </section>
</main>
</body>
</html>
```